Business Cards for new orthopaedic surgery practice

My husband and I are starting our own orthopaedic surgery practice. We are looking for a business card that is uniform, but one will have my name/title and the other will have his. You can just create one design with my name on it for now. But when I choose your design as the winning design I will ask that you add another copy with his name/title.

We are looking for classy, simple, elite all in one. We like dark blues/a little gold/yellow. Something that goes with our logo. We want our logo incorporated. Here is all the info you need:
Business name: RV Bone & Vitality Center
Location: 38517 North Willowmere Ave
Harbor Glen, FL 33990
Phone: 954-218-4063
Fax: 954-582-7341
Email: info@myrvbonecare.example

Names: Lydia Vance, M.D.
Board Certified Hand and Upper Extremity Surgeon

Ebo Dansu, M.D.
Board Certified Hip & Knee Replacement/General Orthopaedic Surgeon

Can decide what you want to put on the back. Maybe a slogan:
Steady Hands. Strong Steps Ahead

I am just going to upload our logo. The only thing is if we select you as the winning design, the location, and phone numbers may change. We will need your help to update that once fully solidified.

Industry/Entity Type

Medical

Contact Information for Business Card

Colors
0054AA
0677BA
7BADD7
CADEEF
E8F1F8
0094D4
00A9DD
6FCCEA
C7EBF8
E9F6FB

Requirements
Must have
• class, appeal,
Should not have
• We want to air on the side of masculine if we are looking at masculine vs. feminine feel. But we still want it classy, sophisticated, and something we will love

```html
<!DOCTYPE html>
<html lang="en">
<head>
<meta charset="utf-8">
<title>RV Bone &amp; Vitality Center – Business Cards</title>
<link href="https://fonts.googleapis.com/css2?family=Montserrat:wght@400;500;600;700&display=swap" rel="stylesheet">
<style>
  :root{
    --navy:#1c2b55;
    --gold:#c9a04e;
    --paper:#ffffff;
    --ink:#1b1b1f;
    --stage:#3a3a3c;
  }
  *{box-sizing:border-box;margin:0;padding:0}
  html,body{width:1200px;height:875px;overflow:hidden}
  body{background:var(--stage);font-family:"Montserrat",sans-serif;position:relative}
  .card{position:absolute;top:283px;width:540px;height:309px;background:var(--paper);border-radius:18px;overflow:hidden;box-shadow:0 10px 30px rgba(0,0,0,.35)}
  .card--back{left:30px}
  .card--front{left:630px}

  /* back: appointment card */
  .appt-title{position:absolute;top:28px;left:0;width:100%;text-align:center;color:var(--navy);font-weight:700;font-size:19px;letter-spacing:.3px}
  .field{position:absolute;display:flex;align-items:flex-end;font-size:12px;font-weight:500;color:var(--ink);letter-spacing:.4px}
  .field .rule{flex:1;border-bottom:1.3px solid var(--navy);margin-left:6px;height:12px}
  .field--name{top:72px;left:40px;width:460px}
  .field--date{top:106px;left:40px;width:230px}
  .field--time{top:106px;left:282px;width:218px}
  .field--time .ampm{margin-left:6px}
  .days-label{position:absolute;top:146px;left:40px;font-size:13px;font-weight:600;color:var(--ink)}
  .days{position:absolute;top:172px;left:40px;right:40px;display:flex;justify-content:space-between}
  .day{display:flex;align-items:center;gap:5px;font-size:10.5px;color:var(--ink)}
  .box{width:13px;height:13px;border:1.5px solid var(--gold);flex:none}
  .slogan{position:absolute;bottom:56px;left:0;width:100%;text-align:center;color:var(--gold);font-weight:700;font-size:16px}

  /* front: contact card */
  .accent-bar{position:absolute;left:0;top:108px;width:16px;height:48px;background:var(--navy)}
  .person{position:absolute;left:30px;top:104px}
  .person-name{font-size:21px;font-weight:700;color:var(--navy)}
  .person-name .cred{color:var(--gold)}
  .person-title{font-size:11px;color:var(--ink);line-height:1.25;margin-top:2px}
  .address{position:absolute;left:30px;top:200px;font-size:11px;line-height:1.3;color:var(--ink)}
  .contact{position:absolute;left:30px;top:236px;list-style:none;font-size:11px;line-height:1.45;color:var(--ink)}
  .contact li{display:flex;align-items:center;gap:6px}
  .contact svg{width:10px;height:10px;fill:var(--gold)}
  .brand{position:absolute;right:26px;top:34px;width:220px;height:220px;display:flex;align-items:center;justify-content:center}
  .brand-ring{position:absolute;inset:0;border:2px solid var(--gold);border-radius:50%}
  .brand-name{font-size:20px;font-weight:700;color:var(--navy);text-align:center;line-height:1.25;width:160px}
</style>
</head>
<body>

<section class="card card--back" aria-label="Appointment card">
  <h2 class="appt-title">YOUR NEXT APPOINTMENT</h2>
  <div class="field field--name">NAME<span class="rule"></span></div>
  <div class="field field--date">DATE<span class="rule"></span></div>
  <div class="field field--time">TIME<span class="rule"></span><span class="ampm">AM/PM</span></div>
  <div class="days-label">DAY OF THE WEEK</div>
  <div class="days">
    <span class="day"><span class="box"></span>MON</span>
    <span class="day"><span class="box"></span>TUE</span>
    <span class="day"><span class="box"></span>WED</span>
    <span class="day"><span class="box"></span>THU</span>
    <span class="day"><span class="box"></span>FRI</span>
    <span class="day"><span class="box"></span>SAT</span>
    <span class="day"><span class="box"></span>SUN</span>
  </div>
  <p class="slogan">Steady Hands. Strong Steps Ahead</p>
</section>

<section class="card card--front" aria-label="Business card">
  <div class="accent-bar"></div>
  <div class="person">
    <h1 class="person-name">Lydia Vance, <span class="cred">M.D.</span></h1>
    <p class="person-title">Board Certified Hand and<br>Upper Extremity Surgeon</p>
  </div>
  <p class="address">38517 North Willowmere Ave<br>Harbor Glen, FL 33990</p>
  <ul class="contact">
    <li><svg viewBox="0 0 10 10"><path d="M2 0h2l1 2.5-1.3 1a6 6 0 0 0 2.8 2.8l1-1.3L10 6v2a2 2 0 0 1-2 2A8 8 0 0 1 0 2a2 2 0 0 1 2-2z"/></svg>954-218-4063</li>
    <li><svg viewBox="0 0 10 10"><path d="M2 0h5v3H2zM0 3.5h10V8H8v2H2V8H0zM3 6.5v2.5h4V6.5z"/></svg>954-582-7341</li>
    <li><svg viewBox="0 0 10 10"><path d="M0 1.5h10v7H0zM1 2.5l4 3 4-3v-.3H1z" fill-rule="evenodd"/></svg>info@myrvbonecare.example</li>
  </ul>
  <div class="brand">
    <span class="brand-ring"></span>
    <span class="brand-name">RV Bone &amp; Vitality Center</span>
  </div>
</section>

</body>
</html>
```